Website for vegan focused blog

A website is needed so that I can launch my new blog in Dubai. It will be mainly vegan focused but also lifestyle based. Wordpress based- i started to build a site on Wordpress but design is not my forte ;)
Main content on the site will be; my recipes, reviews of products/restaurants, lifestyle posts and travel.
For this I ask for a homepage design, a recipe design page that includes a recipe card and a generic page for posts that can show pictures and videos. Also a contact me page.
Main headers should be: Home, Recipes and happy for suggestions.
Must look clean and neat but appealing, happy for minimalist look. I like pink and grey colours. Must be Wordpress compatible.
Have attached a couple of example posts for reference
Must have social links etc.
name of blog is: Maren by the dunes
Other blogs I like are: https://quietladleoven.com/ https://wellfernkitchen.com/ https://wellfernkitchen.com/ https://www.ohladycakes.com/https://beetsatsupper.com/ https://dorintalve.com/

Target Market(s)

Residents in the UAE. General individuals interested in vegan meals, plant based nutrition, travel and reviews.

Number of Pages Required

4 page

Colors
eea4c8
eda3c7
f9d9e8
dbdbdb
aaaaaa
d5d5d5

Requirements
Must have
• Recipe page- must include recipe card plug in option
• Social media integration
• Email sign ups

```html
<!DOCTYPE html>
<html lang="en">
<head>
<meta charset="utf-8">
<title>Contact — Maren by the dunes</title>
<link rel="stylesheet" href="https://fonts.googleapis.com/css2?family=Lato:wght@400;700&family=Playfair+Display:ital,wght@0,400;0,700;1,400;1,700&display=swap">
<style>
  :root {
    --pink: #eea4c8;
    --pink-soft: #f9d9e8;
    --line: #dbdbdb;
    --line-light: #e8e8e8;
    --muted: #aaaaaa;
    --text: #555555;
    --heading: #444444;
    --footer-bg: #fafafa;
    --white: #ffffff;
  }
  * { box-sizing: border-box; margin: 0; padding: 0; }
  html, body { width: 1200px; height: 914px; overflow: hidden; background: var(--white); }
  body { position: relative; font-family: "Lato", sans-serif; color: var(--text); }

  .brand {
    position: absolute; left: 0; right: 0; top: 28px;
    text-align: center; font-family: "Playfair Display", serif; font-weight: 400;
    font-size: 38px; color: var(--pink); letter-spacing: 0.5px;
  }
  .brand-dot { display: inline-block; width: 10px; height: 10px; border-radius: 50%; background: var(--pink); margin-right: 12px; vertical-align: middle; }

  .main-nav {
    position: absolute; left: 0; top: 115px; width: 1200px; height: 38px;
    border-top: 1px solid var(--line-light); border-bottom: 1px solid var(--line-light);
  }
  .main-nav ul { list-style: none; display: flex; justify-content: center; gap: 36px; padding-top: 9px; padding-left: 0; }
  .main-nav a { font-family: "Playfair Display", serif; font-style: italic; font-weight: 700; font-size: 12px; color: #666; text-decoration: none; letter-spacing: 0.3px; }
  .search-icon { position: absolute; left: 954px; top: 12px; }

  .dropdown {
    position: absolute; left: 617px; top: 152px; width: 111px;
    background: var(--white); border: 1px solid var(--line-light);
    box-shadow: 0 2px 4px rgba(0,0,0,0.06); list-style: none; z-index: 2;
  }
  .dropdown::before {
    content: ""; position: absolute; top: -5px; left: 51px; width: 8px; height: 8px;
    background: var(--white); border-left: 1px solid var(--line-light); border-top: 1px solid var(--line-light); transform: rotate(45deg);
  }
  .dropdown li { height: 24.5px; line-height: 24px; text-align: center; border-top: 1px solid var(--line-light);
    font-family: "Playfair Display", serif; font-style: italic; font-weight: 700; font-size: 12px; color: #666; }
  .dropdown li:first-child { border-top: none; }

  .page { position: absolute; left: 233px; top: 172px; width: 732px; }
  .page-title { font-family: "Playfair Display", serif; font-weight: 700; font-size: 29px; color: var(--pink); }
  .intro { margin-top: 6px; padding-left: 2px; font-size: 10px; line-height: 15px; color: #666; width: 640px; }

  .contact-list { list-style: none; margin-top: 22px; }
  .contact-list li { position: relative; padding-left: 25px; font-weight: 700; font-size: 10.3px; color: var(--heading); line-height: 12px; margin-bottom: 15px; }
  .contact-list svg { position: absolute; left: 2px; top: 1px; }

  .contact-form { position: absolute; left: 234px; top: 375px; width: 731px; }
  .field { position: absolute; height: 25px; border: 1px solid #d5d5d5; background: var(--white);
    font-size: 8.6px; color: #888; padding: 7px 0 0 24px; }
  .field svg { position: absolute; left: 8px; top: 8px; }
  .field-message { height: 100px; }
  .send-btn { position: absolute; left: 0; top: 196px; width: 90px; height: 25px; background: var(--pink); color: var(--white);
    font-weight: 700; font-size: 8.4px; letter-spacing: 0.6px; text-align: center; line-height: 25px; }

  .site-footer { position: absolute; left: 0; top: 713px; width: 1200px; height: 201px; background: var(--footer-bg); }
  .footer-brand { position: absolute; left: 0; right: 0; top: 41px; text-align: center;
    font-family: "Playfair Display", serif; font-weight: 400; font-size: 30px; color: var(--pink); }
  .social { position: absolute; top: 112px; left: 526px; display: flex; gap: 9px; }
  .social span { width: 22.5px; height: 22.5px; border-radius: 50%; background: var(--pink); display: block; }
  .footer-bottom { position: absolute; left: 0; top: 164px; width: 1200px; height: 37px; border-top: 1px solid #eeeeee;
    text-align: center; font-size: 8px; color: var(--muted); line-height: 44px; }
</style>
</head>
<body>

<header>
  <div class="brand"><span class="brand-dot"></span>Maren by the dunes</div>
  <nav class="main-nav">
    <ul>
      <li><a href="#">Home</a></li>
      <li><a href="#">About me</a></li>
      <li><a href="#">Recipes</a></li>
      <li><a href="#">Lifestyle</a></li>
      <li><a href="#">Contact</a></li>
    </ul>
    <svg class="search-icon" width="12" height="12" viewBox="0 0 12 12" aria-hidden="true">
      <circle cx="5" cy="5" r="3.8" fill="none" stroke="#555" stroke-width="1.6"/>
      <line x1="7.8" y1="7.8" x2="11" y2="11" stroke="#555" stroke-width="1.8" stroke-linecap="round"/>
    </svg>
  </nav>
  <ul class="dropdown">
    <li>Travel</li>
    <li>Reviews</li>
    <li>Fitness</li>
  </ul>
</header>

<main class="page">
  <h1 class="page-title">Get In Touch</h1>
  <p class="intro">Ut a lorem finibus urna tincidunt lacinia. Nullam hendrerit, nisl in elementum rutrum, sapien vitae tempor ornare purus, nec cursus nulla nisi sed mi. Quisque et purus volutpat, maximus dolor quis, aliquet turpis.</p>

  <ul class="contact-list">
    <li>
      <svg width="11" height="11" viewBox="0 0 12 12" aria-hidden="true"><path d="M2.5 1 L4.5 3.5 L3.5 5 Q5 7.5 7 8.5 L8.5 7.5 L11 9.5 L9.5 11 Q4 10 1 2.5 Z" fill="none" stroke="var(--pink)" stroke-width="0.9" stroke-linejoin="round"/></svg>
      01 98 76 54 32
    </li>
    <li>
      <svg width="11" height="10" viewBox="0 0 12 10" aria-hidden="true"><rect x="0.5" y="1" width="11" height="8" fill="none" stroke="var(--pink)" stroke-width="0.9"/><path d="M0.5 1 L6 5.5 L11.5 1" fill="none" stroke="var(--pink)" stroke-width="0.9"/></svg>
      hello@marendunes.com
    </li>
    <li style="margin-top:18px">
      <svg width="10" height="12" viewBox="0 0 10 12" aria-hidden="true"><path d="M5 11.5 Q1 7 1 4.5 A4 4 0 0 1 9 4.5 Q9 7 5 11.5 Z" fill="none" stroke="var(--pink)" stroke-width="0.9"/><circle cx="5" cy="4.5" r="1.4" fill="none" stroke="var(--pink)" stroke-width="0.9"/></svg>
      1234 Lorem Ipsum Dolor Sit<br>Magna tempus - Interdum
    </li>
  </ul>
</main>

<form class="contact-form">
  <div class="field" style="left:0;top:0;width:357px">
    <svg width="9" height="9" viewBox="0 0 10 10" aria-hidden="true"><circle cx="5" cy="3" r="2.3" fill="none" stroke="var(--pink)" stroke-width="0.9"/><path d="M1 9.5 Q1 6 5 6 Q9 6 9 9.5 Z" fill="none" stroke="var(--pink)" stroke-width="0.9"/></svg>
    Your name
  </div>
  <div class="field" style="left:375px;top:0;width:356px">
    <svg width="9" height="9" viewBox="0 0 12 12" aria-hidden="true"><path d="M2.5 1 L4.5 3.5 L3.5 5 Q5 7.5 7 8.5 L8.5 7.5 L11 9.5 L9.5 11 Q4 10 1 2.5 Z" fill="none" stroke="var(--pink)" stroke-width="1"/></svg>
    Your phone
  </div>
  <div class="field" style="left:0;top:40px;width:357px">
    <svg width="9" height="8" viewBox="0 0 12 10" aria-hidden="true"><rect x="0.5" y="1" width="11" height="8" fill="none" stroke="var(--pink)" stroke-width="1"/><path d="M0.5 1 L6 5.5 L11.5 1" fill="none" stroke="var(--pink)" stroke-width="1"/></svg>
    Your email
  </div>
  <div class="field" style="left:375px;top:40px;width:356px">
    <svg width="9" height="9" viewBox="0 0 10 10" aria-hidden="true"><path d="M1 9 L1.5 6.8 L7.3 1 L9 2.7 L3.2 8.5 Z" fill="none" stroke="var(--pink)" stroke-width="0.9"/></svg>
    Subject
  </div>
  <div class="field field-message" style="left:0;top:81px;width:731px">
    <svg width="9" height="9" viewBox="0 0 10 10" aria-hidden="true"><path d="M0.8 1 H9.2 V6.8 H4 L1.8 9 V6.8 H0.8 Z" fill="none" stroke="var(--pink)" stroke-width="0.9"/></svg>
    Your message
  </div>
  <div class="send-btn">SEND MESSAGE</div>
</form>

<footer class="site-footer">
  <div class="footer-brand">Maren by the dunes</div>
  <div class="social" aria-label="Social links">
    <span></span><span></span><span></span><span></span><span></span>
  </div>
  <div class="footer-bottom">Copyright © 2018 Maren by the dunes. All Right Reserved. Privacy Policy | Terms of Service</div>
</footer>

</body>
</html>
```